Business Card for Coastal Tundrabridge Advisory

We need a business card for Coastal Tundrabridge Advisory. The company website address is provided below. The company logo is attached. We provide specialized permafrost services to the mining, transportation, and oil & gas industries. The card should be prepared for:
Matthias Korhonen, PhD.
Coastal Tundrabridge Advisory
PO Box 418259
Quillwater, Alaska 99642
Direct: +1-907-555-0143
Email: mkorhonen@tundrabridgeadvisory.example
Website: www.coastaltundrabridgeadvisory.example

```html
<!DOCTYPE html>
<html lang="en">
<head>
<meta charset="utf-8">
<title>Coastal Tundrabridge Advisory – Business Card</title>
<link rel="stylesheet" href="https://fonts.googleapis.com/css2?family=Montserrat:wght@400;500;600;700&display=swap">
<style>
  :root {
    --backdrop: #e7e3dc;
    --card-white: #ffffff;
    --ink-navy: #111820;
    --text-dark: #15191f;
    --text-light: #ffffff;
    --text-muted: #d7dbe0;
  }
  * { margin: 0; padding: 0; box-sizing: border-box; }
  html, body {
    width: 900px; height: 1200px; overflow: hidden;
    background: var(--backdrop);
    font-family: "Montserrat", sans-serif;
  }
  .canvas { position: relative; width: 900px; height: 1200px; }

  .card {
    position: absolute; left: 80px; width: 742px; height: 440px;
    border-radius: 22px; overflow: hidden;
  }
  .card-front { top: 131px; background: var(--card-white); }
  .card-back { top: 638px; background: var(--ink-navy); }

  .front-wordmark {
    position: absolute; left: 40px; top: 218px; width: 270px;
    text-align: center; color: var(--ink-navy);
    font-weight: 700; font-size: 17px; letter-spacing: 1.5px; line-height: 1.35;
    text-transform: uppercase;
  }
  .divider {
    position: absolute; left: 316px; top: 160px;
    width: 2px; height: 145px; background: var(--ink-navy);
  }
  .person-name {
    position: absolute; left: 328px; top: 158px;
    font-size: 22px; font-weight: 700; color: var(--text-dark);
  }
  .person-title {
    position: absolute; left: 328px; top: 188px;
    font-size: 15px; font-weight: 500; color: var(--text-dark);
  }
  .contact-list { position: absolute; left: 330px; top: 220px; list-style: none; }
  .contact-item {
    display: flex; align-items: center; height: 30.5px;
    font-size: 15px; color: var(--text-dark);
  }
  .contact-icon { width: 16px; height: 16px; margin-right: 14px; fill: var(--ink-navy); }

  .address-band {
    position: absolute; left: 0; top: 369px; width: 100%; height: 53px;
    background: var(--ink-navy); color: var(--text-light);
    display: flex; align-items: center; justify-content: center;
    font-size: 16px; padding-right: 70px;
  }

  .back-wordmark {
    position: absolute; left: 0; top: 178px; width: 100%;
    text-align: center; color: var(--text-light);
    font-weight: 700; font-size: 36px; letter-spacing: 3px; line-height: 1.3;
    text-transform: uppercase;
  }
</style>
</head>
<body>
<main class="canvas">
  <section class="card card-front">
    <div class="front-wordmark">Coastal Tundrabridge<br>Advisory</div>
    <div class="divider"></div>
    <h1 class="person-name">Matthias Korhonen, PhD.</h1>
    <p class="person-title">Managing Director</p>
    <ul class="contact-list">
      <li class="contact-item">
        <svg class="contact-icon" viewBox="0 0 24 24" aria-hidden="true"><path d="M6.6 10.8a15.1 15.1 0 0 0 6.6 6.6l2.2-2.2a1 1 0 0 1 1-.25 11.4 11.4 0 0 0 3.6.57 1 1 0 0 1 1 1V20a1 1 0 0 1-1 1A17 17 0 0 1 3 4a1 1 0 0 1 1-1h3.5a1 1 0 0 1 1 1c0 1.25.2 2.45.57 3.57a1 1 0 0 1-.25 1z"/></svg>
        +1-907-555-0143
      </li>
      <li class="contact-item">
        <svg class="contact-icon" viewBox="0 0 24 24" aria-hidden="true"><path d="M3 6h18v12H3z M3 6l9 7 9-7" fill="none" stroke="#111820" stroke-width="0"/><path d="M3 5h18a1 1 0 0 1 1 1v.5l-10 6.5L2 6.5V6a1 1 0 0 1 1-1zm-1 4l10 6.5L22 9v9a1 1 0 0 1-1 1H3a1 1 0 0 1-1-1z"/></svg>
        mkorhonen@tundrabridgeadvisory.example
      </li>
      <li class="contact-item">
        <svg class="contact-icon" viewBox="0 0 24 24" aria-hidden="true"><circle cx="12" cy="12" r="9" fill="none" stroke="#111820" stroke-width="2"/><path d="M3 12h18M12 3c3 3 3 15 0 18M12 3c-3 3-3 15 0 18" fill="none" stroke="#111820" stroke-width="1.6"/></svg>
        www.coastaltundrabridgeadvisory.example
      </li>
    </ul>
    <div class="address-band">PO Box 418259 Quillwater, Alaska 99642</div>
  </section>

  <section class="card card-back">
    <div class="back-wordmark">Coastal Tundrabridge<br>Advisory</div>
  </section>
</main>
</body>
</html>
```